Gobal construction supply company needs new business card design

I need a business card design for my global supply company using an existing logo. i will be looking to print these on rounded corner cards with the black background version of my logo on the back. on the front white background, my logo again and my simple details.

```html
<!DOCTYPE html>
<html lang="en">
<head>
<meta charset="utf-8">
<title>Northgate Build Supply – Business Card</title>
<link rel="stylesheet" href="https://fonts.googleapis.com/css2?family=Roboto:wght@400;500;700&display=swap">
<style>
  :root {
    --backdrop: #2a2a2a;
    --card-white: #f4f4f4;
    --card-black: #1c1c1c;
    --ink: #111111;
    --ink-soft: #4a4a4a;
    --accent: #d90000;
    --rule: #cfcfcf;
    --on-dark: #f2f2f2;
  }
  * { margin: 0; padding: 0; box-sizing: border-box; }
  html, body {
    width: 1200px; height: 960px; overflow: hidden;
    background: var(--backdrop);
    font-family: "Roboto", Arial, sans-serif;
  }
  .stage { position: relative; width: 1200px; height: 960px; }

  .card {
    position: absolute; width: 600px; height: 342px;
    border-radius: 20px; overflow: hidden;
  }
  .card-front { left: 186px; top: 113px; background: var(--card-white); }
  .card-back { left: 434px; top: 511px; background: var(--card-black); }

  /* front: brand block */
  .brand {
    position: absolute; left: 30px; top: 110px; width: 270px;
    text-align: center;
  }
  .brand-dot {
    display: block; width: 20px; height: 20px; margin: 0 auto 14px;
    border-radius: 50%; background: var(--accent);
  }
  .brand-name {
    font-weight: 700; font-size: 20px; color: var(--ink);
    letter-spacing: 0.2px; line-height: 1.2;
  }
  .brand-rule {
    height: 2px; background: var(--accent); margin: 10px 12px 0;
  }

  .divider {
    position: absolute; left: 307px; top: 72px; width: 1px; height: 198px;
    background: var(--rule);
  }

  /* front: contact block */
  .contact { position: absolute; left: 331px; top: 73px; }
  .person-name { font-size: 22px; font-weight: 500; color: var(--ink); letter-spacing: 0.3px; line-height: 26px; }
  .person-role { font-size: 14.5px; font-weight: 500; color: var(--accent); line-height: 18px; }
  .address { margin-top: 12px; font-size: 14.5px; color: var(--ink-soft); line-height: 19px; }
  .lines { margin-top: 10px; list-style: none; }
  .lines li {
    display: flex; align-items: center; gap: 8px;
    font-size: 14.5px; color: var(--ink-soft); line-height: 19px;
  }
  .lines svg { width: 14px; height: 14px; fill: var(--ink); flex: none; }

  .stripe-dark {
    position: absolute; left: 0; bottom: 0; width: 355px; height: 12px;
    background: var(--ink);
  }
  .stripe-red {
    position: absolute; right: 0; bottom: 0; width: 245px; height: 12px;
    background: var(--accent);
  }

  /* back */
  .back-brand {
    position: absolute; left: 0; right: 0; top: 112px;
    text-align: center;
  }
  .back-brand .brand-dot { width: 34px; height: 34px; margin-bottom: 22px; }
  .back-brand .brand-name { color: var(--on-dark); font-size: 34px; }
  .back-url {
    position: absolute; left: 0; right: 0; top: 291px;
    text-align: center; font-size: 14px; color: var(--on-dark);
    letter-spacing: 2.6px;
  }
</style>
</head>
<body>
<div class="stage">

  <section class="card card-front">
    <div class="brand">
      <span class="brand-dot"></span>
      <div class="brand-name">NORTHGATE BUILD SUPPLY</div>
      <div class="brand-rule"></div>
    </div>

    <div class="divider"></div>

    <div class="contact">
      <div class="person-name">DANIEL REYES</div>
      <div class="person-role">CEO/FOUNDER</div>
      <div class="address">1420 Harbor View Road<br>Portland, Oregon 97201</div>
      <ul class="lines">
        <li><svg viewBox="0 0 16 16"><path d="M3.5 1l2.5 3-1.5 2c1 2 2.5 3.5 4.5 4.5l2-1.5 3 2.5-1.5 2.5C7 15 1 9 1 2.5z"/></svg>555 210 4830</li>
        <li><svg viewBox="0 0 16 16"><path d="M4 0h8a1 1 0 0 1 1 1v14a1 1 0 0 1-1 1H4a1 1 0 0 1-1-1V1a1 1 0 0 1 1-1zm1 2v10h6V2zm3 11a1 1 0 1 0 0 2 1 1 0 0 0 0-2z"/></svg>555 318 7742</li>
        <li><svg viewBox="0 0 16 16"><path d="M4 1h8v4H4zM1 6h14v7h-3v2H4v-2H1zm4 5v3h6v-3z"/></svg>555 644 1095</li>
        <li><svg viewBox="0 0 16 16"><path d="M1 3h14v10H1zm1.5 1.5L8 9l5.5-4.5z"/></svg>daniel@northgatebuild.com</li>
        <li><svg viewBox="0 0 16 16"><path d="M8 1a7 7 0 1 0 0 14A7 7 0 0 0 8 1zm-1 2.2v2.3L4.8 7.3 3 6.5A5.3 5.3 0 0 1 7 3.2zm2.5 9.9V11l2-2.2 1.6.6a5.3 5.3 0 0 1-3.6 3.7z"/></svg>www.northgatebuild.com</li>
      </ul>
    </div>

    <div class="stripe-dark"></div>
    <div class="stripe-red"></div>
  </section>

  <section class="card card-back">
    <div class="back-brand">
      <span class="brand-dot"></span>
      <div class="brand-name">NORTHGATE BUILD SUPPLY</div>
    </div>
    <div class="back-url">www.northgatebuild.com</div>
  </section>

</div>
</body>
</html>
```